Online homewares store needs a web design

We need a web design for a new high-end online homewares store. We are starting small with only 5 major categories.

Rugs
Bathe
Dine
Decorative
Sleep

This is just for design. No coding needed.

Please make high-end, sophisticated and minimal.

I have included some pictures to give you an idea of the products. I would like to showcase some of the pictures on the web page.

The website will be using an e-commerce function.

I have included the logo studio nine harbors.

I like this website
http://mapleandquarrylane.example/

or

borvanest.example.au

Simple but effective - not too busy

Project Deadline Extended
Reason: I would like to extend my deadline to give designers more time to do quality work - as requested!! Thanks.

Target Market(s)

Females in the age bracket of 25-45

Males who are very house proud 25-45

Industry/Entity Type

Store

Requirements
Must have
• Upmarket

```html
<!DOCTYPE html>
<html lang="en">
<head>
<meta charset="utf-8">
<title>studio nine harbors — Home</title>
<link href="https://fonts.googleapis.com/css2?family=Questrial&family=Open+Sans:ital,wght@0,400;0,700;1,400&family=Montserrat:wght@700&display=swap" rel="stylesheet">
<style>
  :root {
    --pink: #e8175d;
    --ink: #222222;
    --grey-text: #555555;
    --rule: #9a9a9a;
    --panel: #f2f2f0;
    --footer: #f4f4f4;
    --footer-base: #e7e5e5;
    --field: #444444;
    --white: #ffffff;
  }
  * { margin: 0; padding: 0; box-sizing: border-box; }
  html, body { width: 954px; height: 1200px; overflow: hidden; background: var(--white); }
  body { position: relative; font-family: "Questrial", "Century Gothic", sans-serif; color: var(--ink); }
  .abs { position: absolute; }

  .top-strip { left: 0; top: 0; width: 954px; height: 6px; background: #111; }
  .header-bg { left: 0; top: 6px; width: 954px; height: 130px; background: linear-gradient(#ececec, #f6f6f6 60%, #ffffff); }

  .utility { top: 9px; font-size: 12px; color: var(--ink); }
  .wordmark { left: 108px; top: 22px; font-size: 37px; letter-spacing: -1px; color: var(--ink); line-height: 1; }
  .social { left: 739px; top: 49px; }

  .nav { top: 81px; height: 23px; font-size: 13px; line-height: 23px; color: var(--ink); }
  .nav--active { left: 108px; width: 59px; background: var(--pink); color: var(--white); text-align: center; }

  .photo { display: block; }
  .hero-left { left: 108px; top: 120px; width: 341px; height: 296px; background: linear-gradient(160deg, #e8e6e2 0%, #6b5652 35%, #a88d74 65%, #8a5a62 100%); }
  .hero-right { left: 451px; top: 120px; width: 395px; height: 296px; background: linear-gradient(180deg, #e9ecea 0%, #c9c6c8 40%, #b58a8e 65%, #d8d4d0 100%); }
  .slider-dots { left: 446px; top: 399px; }

  .section-title { font-size: 22px; color: var(--grey-text); }
  .section-rule { height: 1.5px; background: var(--rule); }

  .tab-panel { left: 108px; top: 501px; width: 738px; height: 189px; background: var(--panel); box-shadow: 0 10px 8px -8px rgba(0,0,0,0.25); border: 1px solid #e4e4e4; }
  .tab { top: 501px; height: 29px; width: 147px; font-size: 14px; line-height: 29px; text-align: center; background: var(--white); border: 1px solid #e0e0e0; color: var(--ink); }
  .tab--active { background: var(--panel); border-color: transparent; line-height: 27px; }

  .card { overflow: hidden; }
  .price-band { position: absolute; left: 0; bottom: 0; width: 100%; height: 22px; background: rgba(60,60,60,0.45); }
  .price { position: absolute; left: 13px; bottom: 1px; font-size: 18px; color: var(--white); line-height: 22px; }
  .add-to-cart { position: absolute; right: 0; bottom: 0; width: 79px; height: 22px; background: var(--pink); color: var(--white); font-family: "Montserrat", sans-serif; font-weight: 700; font-size: 9px; text-align: center; line-height: 22px; }
  .card-title { position: absolute; left: 14px; bottom: 48px; font-family: "Montserrat", sans-serif; font-weight: 700; font-size: 14px; color: #111; text-shadow: 0 0 3px #fff; }

  .footer-bg { left: 0; top: 1001px; width: 954px; height: 171px; background: var(--footer); }
  .footer-base { left: 0; top: 1172px; width: 954px; height: 28px; background: var(--footer-base); font-family: "Open Sans", sans-serif; font-size: 9px; text-align: center; line-height: 28px; color: var(--ink); }
  .footer-heading { top: 1008px; font-family: "Open Sans", sans-serif; font-style: italic; font-size: 18px; color: var(--pink); }
  .footer-link { font-size: 13px; color: var(--ink); }
  .footer-sublink { font-size: 11px; color: var(--ink); }
  .footer-divider { top: 1055px; width: 1px; height: 100px; background: #e0e0e0; }
  .field { left: 427px; width: 181px; height: 22px; background: var(--field); color: #bbb; font-family: "Open Sans", sans-serif; font-size: 9px; line-height: 22px; padding-left: 10px; }
  .send { left: 427px; top: 1099px; width: 181px; height: 22px; background: var(--pink); color: var(--white); font-family: "Open Sans", sans-serif; font-size: 11px; text-align: center; line-height: 22px; }
  .pay-card { width: 47px; height: 30px; border: 1px solid #aaa; background: #dcdcdc; }
</style>
</head>
<body>
  <div class="abs top-strip"></div>
  <div class="abs header-bg"></div>

  <div class="abs utility" style="left:707px">View Cart</div>
  <div class="abs utility" style="left:778px">Items / $0.00</div>

  <div class="abs wordmark">studio nine harbors</div>

  <svg class="abs social" width="106" height="24" viewBox="0 0 106 24" aria-label="Social links">
    <g fill="none" stroke="#e8175d" stroke-width="1.2">
      <circle cx="11" cy="12" r="10.5"/>
      <circle cx="38" cy="12" r="10.5"/>
      <circle cx="66" cy="12" r="10.5"/>
      <circle cx="92" cy="12" r="10.5"/>
    </g>
  </svg>

  <div class="abs nav nav--active">Home</div>
  <div class="abs nav" style="left:189px">About Us</div>
  <div class="abs nav" style="left:276px">Products</div>
  <div class="abs nav" style="left:361px">Catalogue</div>
  <div class="abs nav" style="left:460px">Contact Us</div>

  <div class="abs photo hero-left" role="img" aria-label="Child's room with a round jute rug ringed by coloured felt circles"></div>
  <div class="abs photo hero-right" role="img" aria-label="Bedroom with a carved headboard, patterned quilt and cushions"></div>
  <svg class="abs slider-dots" width="62" height="14" viewBox="0 0 62 14" aria-label="Slide indicators">
    <rect x="0" y="1" width="12" height="12" fill="#9c2a3a"/>
    <rect x="16" y="1" width="12" height="12" fill="none" stroke="#fff" stroke-width="1.5"/>
    <rect x="32" y="1" width="12" height="12" fill="none" stroke="#fff" stroke-width="1.5"/>
    <rect x="48" y="1" width="12" height="12" fill="none" stroke="#fff" stroke-width="1.5"/>
  </svg>

  <div class="abs section-title" style="left:107px;top:440px">Products Categories</div>
  <div class="abs section-rule" style="left:316px;top:459px;width:530px"></div>

  <div class="abs tab-panel"></div>
  <div class="abs tab tab--active" style="left:108px">Rugs</div>
  <div class="abs tab" style="left:255px">Dine</div>
  <div class="abs tab" style="left:402px">Bathe</div>
  <div class="abs tab" style="left:549px">Sleep</div>
  <div class="abs tab" style="left:696px;width:150px">Decorative</div>

  <div class="abs card" style="left:116px;top:544px;width:175px;height:131px">
    <div class="photo" role="img" aria-label="Striped woven bath towels with fringes" style="width:100%;height:100%;background:linear-gradient(135deg,#b8566e,#8a86a8 50%,#c7a65a)"></div>
    <div class="price-band"></div><div class="price">$50.95</div><div class="add-to-cart">Add to Cart</div>
  </div>
  <div class="abs card" style="left:298px;top:544px;width:175px;height:131px">
    <div class="photo" role="img" aria-label="Colourful dotted towels stacked with soap" style="width:100%;height:100%;background:linear-gradient(135deg,#6a4a7a,#c46478 50%,#d8d2cc)"></div>
    <div class="price-band"></div><div class="price">$50.95</div><div class="add-to-cart">Add to Cart</div>
  </div>
  <div class="abs card" style="left:481px;top:544px;width:175px;height:131px">
    <div class="photo" role="img" aria-label="Round jute rug with coloured felt circle border" style="width:100%;height:100%;background:linear-gradient(160deg,#4a3a3c,#9a7e6a 55%,#6a4a48)"></div>
    <div class="price-band"></div><div class="price">$50.95</div><div class="add-to-cart">Add to Cart</div>
  </div>
  <div class="abs card" style="left:663px;top:544px;width:175px;height:131px">
    <div class="photo" role="img" aria-label="Natural jute rug with scalloped flower edge" style="width:100%;height:100%;background:linear-gradient(160deg,#f4efe6,#d6c09a 55%,#efe8dc)"></div>
    <div class="price-band"></div><div class="price">$50.95</div><div class="add-to-cart">Add to Cart</div>
  </div>

  <div class="abs section-title" style="left:106px;top:723px">Best Selling Items</div>
  <div class="abs section-rule" style="left:282px;top:741px;width:564px"></div>

  <div class="abs card" style="left:108px;top:757px;width:179px;height:208px">
    <div class="photo" role="img" aria-label="Jute rug with felt circles on a timber floor" style="width:100%;height:100%;background:linear-gradient(160deg,#b87a8a,#c9ae8a 45%,#9a7a5a)"></div>
    <div class="card-title">Lorem Ipsum</div>
    <div class="price-band"></div><div class="price">$50.95</div><div class="add-to-cart">Add to Cart</div>
  </div>
  <div class="abs card" style="left:295px;top:757px;width:178px;height:208px">
    <div class="photo" role="img" aria-label="Stack of patchwork floor cushions" style="width:100%;height:100%;background:linear-gradient(180deg,#b08a5a,#8f8a6a 45%,#a86a52 75%,#c8bca8)"></div>
    <div class="card-title">Lorem Ipsum</div>
    <div class="price-band"></div><div class="price">$50.95</div><div class="add-to-cart">Add to Cart</div>
  </div>
  <div class="abs card" style="left:481px;top:757px;width:179px;height:208px">
    <div class="photo" role="img" aria-label="String of multicoloured felt balls on wood" style="width:100%;height:100%;background:linear-gradient(135deg,#a8704a,#b85a6a 45%,#7a8a6a 75%,#9a6a44)"></div>
    <div class="card-title">Lorem Ipsum</div>
    <div class="price-band"></div><div class="price">$50.95</div><div class="add-to-cart">Add to Cart</div>
  </div>
  <div class="abs card" style="left:667px;top:757px;width:179px;height:208px">
    <div class="photo" role="img" aria-label="Pink and purple patterned cushions on a white carved bench" style="width:100%;height:100%;background:linear-gradient(170deg,#e8e6e2 0%,#c9a2bc 50%,#9a6a92 80%,#d8d2d4)"></div>
    <div class="card-title">Lorem Ipsum</div>
    <div class="price-band"></div><div class="price">$50.95</div><div class="add-to-cart">Add to Cart</div>
  </div>

  <div class="abs footer-bg"></div>

  <div class="abs footer-heading" style="left:108px">Site map</div>
  <div class="abs footer-link" style="left:108px;top:1039px">Home</div>
  <div class="abs footer-link" style="left:108px;top:1063px">About Us</div>
  <div class="abs footer-link" style="left:108px;top:1087px">Catalogue</div>
  <div class="abs footer-link" style="left:108px;top:1110px">Contact Us</div>
  <div class="abs footer-link" style="left:210px;top:1039px">Products</div>
  <div class="abs footer-sublink" style="left:221px;top:1064px">-- Rugs</div>
  <div class="abs footer-sublink" style="left:221px;top:1085px">-- Bathe</div>
  <div class="abs footer-sublink" style="left:221px;top:1106px">-- Dine</div>
  <div class="abs footer-sublink" style="left:221px;top:1127px">-- Decorative</div>
  <div class="abs footer-sublink" style="left:221px;top:1148px">-- Sleep</div>

  <div class="abs footer-divider" style="left:358px"></div>
  <div class="abs footer-divider" style="left:678px"></div>

  <div class="abs footer-heading" style="left:428px">Newsletter</div>
  <div class="abs field" style="top:1043px">Name</div>
  <div class="abs field" style="top:1071px">Email</div>
  <div class="abs send">SEND</div>

  <div class="abs footer-heading" style="left:709px">Payment Options</div>
  <div class="abs pay-card" style="left:747px;top:1042px" aria-label="Accepted card"></div>
  <div class="abs pay-card" style="left:798px;top:1042px" aria-label="Accepted card"></div>
  <div class="abs pay-card" style="left:747px;top:1079px" aria-label="Accepted card"></div>
  <div class="abs pay-card" style="left:798px;top:1079px" aria-label="Accepted card"></div>

  <div class="abs footer-base">Copyright © 2014 studio nine harbors &nbsp;|&nbsp; All rights reserved.</div>
</body>
</html>
```